Moravel Aesthetic Doctor

I require an elegant, luxurious looking business card for my aesthetic business. I am a doctor and that will set me aside from competitors. I am planning to provide home and spa based treatments to clients with high expectations. I have attached my logo.

```html
<!DOCTYPE html>
<html lang="en">
<head>
<meta charset="utf-8">
<title>Moravel Aesthetic Doctor – Business Card</title>
<link href="https://fonts.googleapis.com/css2?family=Arimo:wght@400;700&display=swap" rel="stylesheet">
<style>
  :root {
    --backdrop: #2a2a2b;
    --card: #0d0d0e;
    --card-edge: #161617;
    --ink-white: #f2f2f2;
    --ink-grey: #b9b9bb;
    --accent-blue: #5cbfec;
    --rule: #4a4a4d;
    --photo-warm: #a8784a;
    --photo-grey: #cfd0d0;
    --photo-skin: #c9a58f;
    --photo-mixed: #c6b8b4;
  }
  * { margin: 0; padding: 0; box-sizing: border-box; }
  html, body {
    width: 1200px; height: 900px; overflow: hidden;
    background: var(--backdrop);
    font-family: "Arimo", Arial, sans-serif;
  }
  .card {
    position: absolute; left: 285px;
    width: 630px; height: 360px;
    background: linear-gradient(160deg, var(--card-edge), var(--card) 60%);
    overflow: hidden;
  }
  .card--front { top: 60px; }
  .card--back { top: 480px; }

  .wordmark { position: absolute; display: flex; align-items: center; gap: 14px; color: var(--accent-blue); font-weight: 400; }
  .wordmark__ring { width: 74px; height: 74px; border: 2px solid #8c8c90; border-radius: 50%; flex: none; }
  .wordmark__name { font-size: 40px; letter-spacing: 3px; line-height: 1; }
  .wordmark__sub { font-size: 15px; letter-spacing: 2.5px; margin-top: 6px; }
  .card--front .wordmark { left: 165px; top: 70px; }
  .card--back .wordmark { left: 345px; top: 120px; }
  .card--back .wordmark__name { font-size: 34px; }
  .card--back .wordmark__sub { font-size: 13px; }

  .divider { position: absolute; height: 1px; background: var(--rule); }
  .divider--wide { left: 150px; right: 40px; top: 188px; }
  .divider--short { left: 40px; width: 210px; top: 268px; }

  .doctor { position: absolute; left: 40px; top: 206px; }
  .doctor__name { font-size: 22px; font-weight: 700; color: var(--ink-grey); }
  .doctor__post { font-size: 15px; font-weight: 400; color: var(--accent-blue); margin-left: 6px; }
  .doctor__diploma { font-size: 15px; color: var(--accent-blue); margin-top: 4px; }

  .contacts { position: absolute; left: 40px; top: 280px; list-style: none; }
  .contacts li { display: flex; align-items: center; gap: 10px; font-size: 14px; color: var(--ink-grey); height: 22px; }
  .contacts svg { width: 15px; height: 15px; flex: none; }

  .social { position: absolute; left: 262px; top: 284px; display: flex; gap: 10px; }
  .social span { width: 24px; height: 24px; border: 1.5px solid var(--accent-blue); border-radius: 50%; }

  .photo-grid { position: absolute; left: 60px; top: 82px; display: grid; grid-template-columns: 130px 130px; grid-template-rows: 95px 95px; gap: 6px; }
  .photo--candles { background: linear-gradient(135deg, #6b5139, var(--photo-warm) 55%, #e8b45c); }
  .photo--towels { background: linear-gradient(135deg, #dcdcdc, var(--photo-grey)); }
  .photo--facial { background: linear-gradient(135deg, var(--photo-skin), #e4c3c3); }
  .photo--products { background: linear-gradient(135deg, #d8d4d2, var(--photo-mixed) 60%, #b04a8c); }

  .tagline { position: absolute; left: 345px; top: 218px; font-size: 12px; letter-spacing: 1.5px; color: var(--ink-white); }
</style>
</head>
<body>

<section class="card card--front" aria-label="Business card front">
  <div class="wordmark">
    <span class="wordmark__ring"></span>
    <div>
      <div class="wordmark__name">MORAVEL</div>
      <div class="wordmark__sub">AESTHETIC DOCTOR</div>
    </div>
  </div>
  <div class="divider divider--wide"></div>

  <div class="doctor">
    <div><span class="doctor__name">Dr Elise Varenne</span><span class="doctor__post">MRCPCH MD</span></div>
    <div class="doctor__diploma">Australasian Diploma of Aesthetic Medicine</div>
  </div>
  <div class="divider divider--short"></div>

  <ul class="contacts">
    <li>
      <svg viewBox="0 0 16 16" fill="none" stroke="#5cbfec" stroke-width="1.6"><path d="M3 2h3l1 3-2 1a8 8 0 0 0 5 5l1-2 3 1v3a1 1 0 0 1-1 1A12 12 0 0 1 2 3a1 1 0 0 1 1-1z"/></svg>
      0800 555 014
    </li>
    <li>
      <svg viewBox="0 0 16 16" fill="none" stroke="#5cbfec" stroke-width="1.6"><rect x="1.5" y="3.5" width="13" height="9"/><path d="M1.5 3.5 8 9l6.5-5.5"/></svg>
      elise@moravel.co.nz
    </li>
    <li>
      <svg viewBox="0 0 16 16" fill="none" stroke="#5cbfec" stroke-width="1.4"><circle cx="8" cy="8" r="6.5"/><ellipse cx="8" cy="8" rx="3" ry="6.5"/><path d="M1.5 8h13M2.5 4.8h11M2.5 11.2h11"/></svg>
      www.moravel.co.nz
    </li>
  </ul>
  <div class="social" aria-label="Social media links"><span></span><span></span></div>
</section>

<section class="card card--back" aria-label="Business card back">
  <div class="photo-grid">
    <div class="photo--candles" role="img" aria-label="Photo of rolled spa towels beside lit candles"></div>
    <div class="photo--towels" role="img" aria-label="Photo of a bath bomb resting on folded white towels"></div>
    <div class="photo--facial" role="img" aria-label="Photo of a gloved facial treatment in progress"></div>
    <div class="photo--products" role="img" aria-label="Photo of skincare products arranged with an orchid"></div>
  </div>
  <div class="wordmark">
    <span class="wordmark__ring"></span>
    <div>
      <div class="wordmark__name">MORAVEL</div>
      <div class="wordmark__sub">AESTHETIC DOCTOR</div>
    </div>
  </div>
  <div class="tagline">HOME AND SPA BASED TREATMENTS</div>
</section>

</body>
</html>
```